EPS Recycling End Market Infographic

We need a two-page visual presentation of new end-market applications for recycled expanded polystyrene (EPS) collected for recycling. This focuses on expanded polystyrene (foam) transport packaging used for international distribution of goods, including pharmaceuticals and food, electronics, appliances and other products that need superior packaging protection.

The bulletin will have examples of 5 major industry categories that benefit from recycled EPS feedstock for reverse engineering to meet current market demand. It will also showcase names of companies that use recycled content EPS in their product manufacturing to legitimize end market adoption. The capability to use recycled EPS in new EPS packaging should be highlighted. We would like this bulletin to demonstrate the widespread application of recycled EPS in different industries and establish credibility that it is being used in a variety of interesting recycled-content products. We welcome creative and interesting font treatments and new trends in graphic design.

Target Market(s)

International Government Agencies, Packaging Engineers, Big Box Retailers, & Environmental Professionals

Industry/Entity Type

Plastic Manufacturers

Font styles to use
Sans Serif

Requirements
Must have
• Visual focus points, multiple examples of products and manufacturers as evidence to the information content
Should not have
• Insufficient white space or outdated design elements (like two-tone gradients).

```html
<!DOCTYPE html>
<html lang="en">
<head>
<meta charset="UTF-8">
<title>How Recycled EPS Finds New Life</title>
<link rel="stylesheet" href="https://fonts.googleapis.com/css2?family=Inter:wght@300;400;500;600&family=Montserrat:wght@400;600;800&display=swap">
<style>
  :root {
    --brown: #62321f;
    --orange: #f4a42b;
    --ink: #4a2a1e;
    --white: #ffffff;
    --photo-workshop: #b9a58c;
    --photo-patio: #6f7d5a;
    --photo-sports: #9a4a38;
    --photo-apparel: #8c4a3e;
    --photo-decor: #a78468;
    --photo-auto: #6d7075;
    --text-font: "Inter", sans-serif;
    --label-font: "Montserrat", sans-serif;
  }
  * { margin: 0; padding: 0; box-sizing: border-box; }
  html, body { width: 1200px; height: 1200px; overflow: hidden; background: var(--white); }
  .canvas { position: relative; width: 1200px; height: 1200px; font-family: var(--text-font); color: var(--ink); }

  /* Left page */
  .page-title { position: absolute; left: 114px; top: 194px; width: 400px; text-align: center; font-size: 36px; font-weight: 500; line-height: 39px; color: var(--brown); }
  .hero-halves { position: absolute; left: 121px; top: 320px; }
  .hero-photo { position: absolute; left: 230px; top: 320px; width: 168px; height: 168px; border-radius: 50%; border: 5px solid var(--brown); background: var(--photo-workshop); }
  .intro { position: absolute; left: 150px; top: 558px; width: 330px; text-align: center; font-size: 15px; font-weight: 300; line-height: 20px; }
  .intro strong { font-weight: 600; color: var(--brown); }
  .rule { position: absolute; left: 160px; width: 309px; height: 1px; background: var(--brown); }
  .section-label { position: absolute; left: 160px; top: 716px; width: 309px; text-align: center; font-size: 16px; font-weight: 600; color: var(--brown); }
  .donut { position: absolute; top: 799px; }
  .donut-value { position: absolute; top: 831px; width: 92px; text-align: center; font-size: 22px; font-weight: 400; color: #111; }
  .stat-caption { position: absolute; top: 930px; font-size: 13px; line-height: 14.6px; font-weight: 300; }
  .stat-caption strong { font-weight: 600; color: var(--brown); }
  .footer-note { position: absolute; left: 160px; top: 1046px; width: 309px; text-align: center; font-size: 11px; font-weight: 400; }

  /* Right page */
  .spotlight { position: absolute; left: 700px; top: 148px; width: 386px; height: 195px; background: var(--brown); color: var(--white); text-align: center; }
  .spotlight h2 { margin-top: 37px; font-size: 35px; font-weight: 500; }
  .spotlight p { margin: 18px auto 0; width: 300px; font-size: 15px; font-weight: 300; line-height: 20px; }
  .spotlight p strong { font-weight: 600; }
  .industry { position: absolute; left: 740px; width: 310px; }
  .industry-photo { position: absolute; left: 0; top: 0; width: 130px; height: 98px; }
  .industry-maker { position: absolute; left: 0; top: 103px; width: 140px; font-family: var(--label-font); font-size: 8.5px; font-weight: 600; color: var(--brown); white-space: nowrap; }
  .industry-text { position: absolute; left: 148px; width: 166px; font-family: var(--label-font); }
  .industry-text h3 { font-size: 13.6px; font-weight: 800; line-height: 17px; color: var(--brown); white-space: nowrap; }
  .industry-text p { margin-top: 8px; font-size: 9.2px; line-height: 12.6px; color: var(--ink); }
  .divider { position: absolute; left: 739px; width: 308px; height: 2.5px; background: var(--orange); }
</style>
</head>
<body>
<div class="canvas">

  <h1 class="page-title">How Recycled EPS Finds New Life</h1>

  <svg class="hero-halves" width="386" height="168" viewBox="0 0 386 168" aria-hidden="true">
    <path d="M0 0 A78 84 0 0 1 0 168 Z" fill="var(--brown)"/>
    <path d="M386 0 A78 84 0 0 0 386 168 Z" fill="var(--brown)"/>
  </svg>
  <div class="hero-photo" role="img" aria-label="Workers sorting colourful foam blocks in a bright recycling workshop"></div>

  <p class="intro">Recycled EPS (expanded polystyrene) plays a crucial role in <strong>sustainability efforts</strong>. This versatile material is used across various industries, promoting a circular economy and reducing waste.</p>

  <div class="rule" style="top:709px"></div>
  <div class="section-label">Recycled EPS</div>
  <div class="rule" style="top:745px"></div>

  <svg class="donut" style="left:160px" width="92" height="92" viewBox="0 0 92 92" aria-hidden="true">
    <circle cx="46" cy="46" r="41" fill="none" stroke="var(--orange)" stroke-width="9"/>
    <path d="M46 5 A41 41 0 0 1 46 87" fill="none" stroke="var(--brown)" stroke-width="9"/>
  </svg>
  <div class="donut-value" style="left:160px">50%</div>

  <svg class="donut" style="left:377px" width="92" height="92" viewBox="0 0 92 92" aria-hidden="true">
    <circle cx="46" cy="46" r="41" fill="none" stroke="var(--brown)" stroke-width="9"/>
    <path d="M7 33.3 A41 41 0 0 1 46 5" fill="none" stroke="var(--orange)" stroke-width="9"/>
  </svg>
  <div class="donut-value" style="left:377px">80%</div>

  <p class="stat-caption" style="left:160px; width:110px;"><strong>30,800 tons EPS</strong> are recycled annually in the U.S.</p>
  <p class="stat-caption" style="left:319px; width:150px; text-align:right;"><strong>EPS can be reused</strong> in new EPS packaging and innovative applications, enhancing its lifecycle.</p>

  <div class="rule" style="top:1032px"></div>
  <p class="footer-note">For more information, go to www.foamloopinfo.com</p>
  <div class="rule" style="top:1074px"></div>

  <section class="spotlight">
    <h2>Industry Spotlight</h2>
    <p><strong>Recycled EPS</strong> contributes significantly to various industries, enhancing sustainability efforts globally.</p>
  </section>

  <article class="industry" style="top:375px">
    <div class="industry-photo" role="img" aria-label="Outdoor lounge furniture on a garden patio" style="background:var(--photo-patio)"></div>
    <div class="industry-maker">Maker: Verdant Patio Co.</div>
    <div class="industry-text" style="top:16px"><h3>OUTDOOR<br>FURNITURE</h3><p>Durable outdoor furniture made from recycled EPS materials.</p></div>
  </article>
  <div class="divider" style="top:494px"></div>

  <article class="industry" style="top:516px">
    <div class="industry-photo" role="img" aria-label="Pile of balls and rackets for various sports" style="background:var(--photo-sports)"></div>
    <div class="industry-maker">Maker: Crestline Boards</div>
    <div class="industry-text" style="top:17px"><h3>SPORTS EQUIPMENT</h3><p>EPS is transformed into high-quality surfboards, showcasing sustainability in sports gear and recreation.</p></div>
  </article>
  <div class="divider" style="top:635px"></div>

  <article class="industry" style="top:658px">
    <div class="industry-photo" role="img" aria-label="Rack of colourful jackets and clothing" style="background:var(--photo-apparel)"></div>
    <div class="industry-maker">Maker: Northloom Apparel</div>
    <div class="industry-text" style="top:19px"><h3>APPAREL</h3><p>Innovative jackets crafted from EPS emphasize eco-friendly practices in the fashion industry.</p></div>
  </article>
  <div class="divider" style="top:776px"></div>

  <article class="industry" style="top:800px">
    <div class="industry-photo" role="img" aria-label="Cosy living room with fireplace and framed pictures" style="background:var(--photo-decor)"></div>
    <div class="industry-maker">Maker: Framewell Studio</div>
    <div class="industry-text" style="top:16px"><h3>HOME DECOR</h3><p>Stylish picture frames created from EPS promote eco-conscious living and design choices.</p></div>
  </article>
  <div class="divider" style="top:918px"></div>

  <article class="industry" style="top:941px">
    <div class="industry-photo" role="img" aria-label="Silver car in an automotive showroom" style="background:var(--photo-auto)"></div>
    <div class="industry-maker">Maker: Rivetra Auto Parts</div>
    <div class="industry-text" style="top:12px"><h3>AUTOMOTIVE</h3><p>Car seat cushions made from recycled EPS improve comfort and sustainability in automotive design.</p></div>
  </article>
  <div class="divider" style="top:1059px"></div>

</div>
</body>
</html>
```